Brochure required

Looking at getting business brochure designed for my solar sales company. i will require a range of products to be listed on the brochure I require a simple/ elegent / professional looking brochure.

I am happy to provide designer with all the required information that must go into the brochure. otherwise please visit www.quillebartow.com.au and view the products which i would like to allocate into the brochure aswell as our company logo and a little about me section

```html
<!DOCTYPE html>
<html lang="en">
<head>
<meta charset="utf-8">
<title>Quillebar – Solar Brochure</title>
<link rel="stylesheet" href="https://fonts.googleapis.com/css2?family=Open+Sans:wght@400;600;700;800&display=swap">
<style>
  :root {
    --canvas: #e9e9ea;
    --paper: #ffffff;
    --paper-shade: #f1f2f3;
    --green: #1fa97c;
    --blue: #1f7fc4;
    --ink: #2f3437;
    --ink-soft: #5a6064;
    --white: #ffffff;
  }
  * { box-sizing: border-box; margin: 0; padding: 0; }
  html, body { width: 1200px; height: 840px; overflow: hidden; }
  body {
    background: var(--canvas);
    font-family: "Open Sans", Arial, sans-serif;
    color: var(--ink);
    position: relative;
  }
  .spread {
    position: absolute;
    left: 60px; top: 38px;
    width: 1080px; height: 764px;
    display: flex;
    box-shadow: 0 10px 30px rgba(0,0,0,.12);
  }
  .page {
    position: relative;
    width: 540px; height: 764px;
    background: var(--paper);
    overflow: hidden;
  }
  .page--front { background: linear-gradient(180deg, var(--paper) 0%, var(--paper-shade) 100%); }

  /* Back page */
  .hero-photo {
    position: absolute; left: 0; top: 0; width: 540px; height: 330px;
    background: linear-gradient(180deg, #2f6fd0 0%, #7fb0ea 38%, #c9d7e8 55%, #3a5aa8 72%, #1f3f86 100%);
  }
  .intro-panel {
    position: absolute; left: 80px; top: 300px; width: 460px; height: 180px;
    background: var(--green);
    color: var(--white);
    padding: 22px 26px 0 30px;
  }
  .intro-panel__title { font-weight: 700; font-size: 15px; margin-bottom: 10px; }
  .intro-panel__text { font-size: 10.5px; line-height: 1.55; }
  .contact-list {
    position: absolute; left: 36px; bottom: 70px;
    list-style: none; font-size: 11.5px; font-weight: 600; color: var(--ink);
  }
  .contact-list li { display: flex; align-items: center; gap: 8px; margin-top: 8px; }
  .icon-dot { width: 14px; height: 14px; flex: none; }

  .brand { position: absolute; text-align: right; }
  .brand__row { display: flex; align-items: center; justify-content: flex-end; gap: 8px; }
  .brand__square { width: 18px; height: 18px; background: var(--green); }
  .brand__name { font-weight: 700; font-size: 26px; color: var(--ink); line-height: 1; }
  .brand__tagline { font-size: 9.5px; color: var(--ink-soft); line-height: 1.2; margin-top: 3px; }
  .brand--back { right: 40px; bottom: 60px; }
  .brand--front { right: 34px; top: 40px; }

  /* Front page */
  .feature-art {
    position: absolute; left: 40px; top: 110px; width: 470px; height: 330px;
    border-radius: 6px;
    background: linear-gradient(135deg, #eef1f5 0%, #6f86c8 30%, #dfe4ea 50%, #3f7f3a 70%, #1f4f22 100%);
  }
  .grey-band {
    position: absolute; left: 0; top: 450px; width: 540px; height: 150px;
    background: linear-gradient(180deg, #e2e4e6, #f3f4f5);
  }
  .feature-panel {
    position: absolute; left: 0; top: 450px; width: 470px; height: 150px;
    background: var(--green);
    color: var(--white);
    padding: 18px 24px 0 24px;
  }
  .feature-panel__title { font-weight: 800; font-size: 22px; letter-spacing: .3px; line-height: 1.1; }
  .feature-panel__subtitle { font-size: 12.5px; letter-spacing: .6px; text-transform: uppercase; margin: 4px 0 10px; }
  .feature-panel__text { font-size: 10.5px; line-height: 1.55; }

  .call-to-action {
    position: absolute; left: 24px; top: 624px;
    font-weight: 700; font-size: 20px; color: var(--blue);
  }
  .address {
    position: absolute; left: 24px; top: 660px;
    display: flex; align-items: center; gap: 8px; font-size: 11.5px; color: var(--ink);
  }
  .visit { position: absolute; left: 24px; top: 688px; display: flex; align-items: center; }
  .visit__label {
    background: var(--blue); color: var(--white); font-size: 11px;
    padding: 4px 14px; border-radius: 12px; position: relative; z-index: 1;
  }
  .visit__url {
    border: 1.5px solid var(--blue); border-radius: 0 12px 12px 0; border-left: none;
    font-size: 11.5px; font-weight: 600; color: var(--ink);
    padding: 3px 16px 3px 22px; margin-left: -12px;
  }
  .email-front {
    position: absolute; right: 30px; top: 693px;
    display: flex; align-items: center; gap: 8px; font-size: 11.5px; font-weight: 600; color: var(--ink);
  }
</style>
</head>
<body>
  <main class="spread">
    <section class="page page--back">
      <div class="hero-photo" role="img" aria-label="Installers fitting solar panels on a roof under a blue cloudy sky"></div>
      <article class="intro-panel">
        <h2 class="intro-panel__title">Quis autem vel</h2>
        <p class="intro-panel__text">Sed quia consequuntur magni dolores eos qui ratione voluptatem sequi nesciunt. Neque porro quisquam est, qui dolorem ipsum quia dolor sit amet, consectetur, adipisci velit, sed quia non numquam eius modi tempora incidunt ut labore et dolore magnam aliquam quaerat voluptatem. Ut enim ad minima veniam, quis nostrum exercitationem ullam corporis suscipit laboriosam, nisi ut aliquid ex ea commodi consequatur.</p>
      </article>
      <ul class="contact-list">
        <li>
          <svg class="icon-dot" viewBox="0 0 14 14"><circle cx="7" cy="7" r="7" fill="#1fa97c"/><circle cx="7" cy="7" r="3.5" fill="none" stroke="#fff" stroke-width="1.2"/><line x1="3.5" y1="7" x2="10.5" y2="7" stroke="#fff" stroke-width="1"/></svg>
          www.quillebartow.com.au
        </li>
        <li>
          <svg class="icon-dot" viewBox="0 0 14 14"><circle cx="7" cy="7" r="7" fill="#1fa97c"/><rect x="3.5" y="4.5" width="7" height="5" fill="none" stroke="#fff" stroke-width="1"/><polyline points="3.5,4.5 7,7.3 10.5,4.5" fill="none" stroke="#fff" stroke-width="1"/></svg>
          info@quillebartow.com.au
        </li>
      </ul>
      <div class="brand brand--back">
        <div class="brand__row"><span class="brand__square"></span><span class="brand__name">Quillebar</span></div>
        <p class="brand__tagline">clean power for homes<br>and business</p>
      </div>
    </section>

    <section class="page page--front">
      <div class="brand brand--front">
        <div class="brand__row"><span class="brand__square"></span><span class="brand__name">Quillebar</span></div>
        <p class="brand__tagline">clean power for homes<br>and business</p>
      </div>
      <div class="feature-art" role="img" aria-label="Solar panel array beside a light bulb holding a green forest"></div>
      <div class="grey-band"></div>
      <article class="feature-panel">
        <h1 class="feature-panel__title">PERSPICIATIS UNDE OMNIS</h1>
        <p class="feature-panel__subtitle">Iste natus error sit voluptatem accusantium</p>
        <p class="feature-panel__text">Doloremque laudantium, totam rem aperiam, eaque ipsa quae ab illo inventore veritatis et quasi architecto beatae vitae dicta sunt explicabo. Nemo enim ipsam voluptatem quia voluptas sit aspernatur aut odit aut fugit.</p>
      </article>
      <p class="call-to-action">For More Information Call 0100-555-278</p>
      <p class="address">
        <svg class="icon-dot" viewBox="0 0 14 14"><circle cx="7" cy="7" r="7" fill="#1fa97c"/><path d="M7 3.2a2.4 2.4 0 0 0-2.4 2.4C4.6 7.4 7 10.6 7 10.6s2.4-3.2 2.4-5A2.4 2.4 0 0 0 7 3.2z" fill="#fff"/><circle cx="7" cy="5.6" r=".9" fill="#1fa97c"/></svg>
        14 Linden Way, Easton Vale, CT 06400
      </p>
      <div class="visit">
        <span class="visit__label">visit us on:</span>
        <span class="visit__url">www.quillebartow.com.au</span>
      </div>
      <p class="email-front">
        <svg class="icon-dot" viewBox="0 0 14 14"><circle cx="7" cy="7" r="7" fill="#1fa97c"/><rect x="3.5" y="4.5" width="7" height="5" fill="none" stroke="#fff" stroke-width="1"/><polyline points="3.5,4.5 7,7.3 10.5,4.5" fill="none" stroke="#fff" stroke-width="1"/></svg>
        info@quillebartow.com.au
      </p>
    </section>
  </main>
</body>
</html>
```